Rebrand & reskin fitbrisko.com (Uncoded)

Fitbrisko.com is a commerce website and app for sports and fitness classes and events. In order to improve its appeal, we invite designers to provide their 'skins' for the landing page, club page and event page. Designers can propose using alternate controls and layouts for these pages, and comment on ways to improve the site's usability. It must remain easy to use on a portrait mobile phone screen, responsive design where necessary to also provide a good experience on desktop.

Please navigate to fitbrisko.com and explore the site, and we look forwards to your suggestions!

Target Market(s)

Primary: Tech-savvy mobile users. Secondary: Desktop users

Industry/Entity Type

Health And Wellness

Number of Pages Required

3 page

Font styles to use
Sans Serif

Colors
ffffff
f37122

Requirements
Must have
• This brief is all about changing the look and feel of the site; the winning design will have an immediate 'wow' factor, yet not sacrifice the ease of finding and paying for classes. It must retain the logo, white and orange must be the primary colours used.
Should not have
• The colour palette must remain roughly as is; for example, a very dark site will not appeal.

```html
<!DOCTYPE html>
<html lang="en">
<head>
<meta charset="utf-8">
<title>Fitbrisko – Welcome</title>
<link href="https://fonts.googleapis.com/css2?family=Open+Sans:wght@400;600&display=swap" rel="stylesheet">
<style>
:root{
  --orange:#f37122;
  --white:#ffffff;
  --dark:#2f3133;
  --bar:#4a4a4a;
  --card:#f1f1f1;
  --text:#333333;
  --muted:#666666;
  --footer:#f4f4f4;
  --footer-bottom:#2b2b2b;
}
*{box-sizing:border-box;margin:0;padding:0}
html,body{width:1200px;height:883px;overflow:hidden}
body{font-family:'Open Sans',Arial,sans-serif;color:var(--text);background:var(--white);position:relative}
.wrap{width:936px;margin:0 auto;position:relative}

/* header */
.site-header{height:70px;background:var(--white)}
.site-header .wrap{display:flex;align-items:center;justify-content:space-between;height:70px}
.brand{display:flex;align-items:center;gap:8px;font-size:24px;font-weight:600;color:var(--orange);letter-spacing:.5px}
.brand-dot{width:22px;height:22px;border-radius:50%;background:var(--orange)}
.main-nav{display:flex;align-items:center;gap:28px;font-size:13px}
.main-nav a{color:#222;text-decoration:none}
.main-nav a.active{color:var(--orange)}
.btn{display:inline-block;font-size:12px;padding:0 18px;line-height:32px;color:var(--white);text-decoration:none;border-radius:2px}
.btn-dark{background:var(--dark)}
.btn-orange{background:var(--orange)}
.main-nav .btn{color:var(--white);margin-left:-4px}
.main-nav .btn + .btn{margin-left:-18px}

/* hero */
.hero{position:relative;height:611px}
.hero-photo{position:absolute;inset:0;background:linear-gradient(180deg,#c9cdd2 0%,#e6e4df 30%,#b9a896 58%,#6e5340 80%,#4a3428 100%)}
.hero-intro{position:relative;text-align:center;padding-top:29px}
.hero-intro h1{font-size:30px;font-weight:400;color:#111;line-height:40px}
.hero-intro p{width:890px;margin:4px auto 0;font-size:11.5px;line-height:18px;color:#555}
.hero-actions{margin-top:8px;display:flex;justify-content:center;gap:9px}
.hero-actions .btn{line-height:32px;font-size:12px;padding:0 13px}

/* tabs & events */
.events-panel{position:absolute;left:132px;top:169px;width:936px}
.tabs{background:var(--bar);display:flex;align-items:stretch;border-bottom:4px solid var(--orange);height:49px;position:relative}
.tab{font-size:20px;color:#ddd;padding:0 18px;line-height:45px}
.tab.current{background:var(--white);color:var(--orange);width:99px;text-align:center;position:relative}
.tab.current::after{content:"";position:absolute;left:42px;bottom:-18px;border:7px solid transparent;border-top-color:var(--orange)}
.tab-arrows{position:absolute;right:27px;top:12px;display:flex;gap:7px}
.tab-arrows span{width:24px;height:21px;border:1px solid #ddd;display:flex;align-items:center;justify-content:center}
.event-grid{background:var(--white);padding:18px 16px 15px;display:grid;grid-template-columns:repeat(3,297px);gap:9px 7px;height:348px}
.event-card{background:var(--card);height:153px;padding:20px 14px 0 17px;display:flex;gap:14px}
.club-badge{width:48px;height:48px;border-radius:50%;flex:none;background:var(--white)}
.event-body h3{font-size:13px;font-weight:400;color:#111}
.event-body h3 small{font-size:10.5px}
.event-club{color:var(--orange);font-size:11.5px;line-height:14px;margin-top:6px}
.event-desc{font-size:9.5px;color:var(--muted);line-height:12.5px;margin-top:7px}
.event-body .btn{margin-top:10px;font-size:10.5px;line-height:27px;padding:0 12px}

/* footer */
.site-footer{height:152px;background:var(--footer)}
.site-footer .wrap{display:flex;padding-top:35px;height:152px}
.f-col{border-right:1px solid #d6d6d6;height:88px}
.f-col h4{font-size:13px;font-weight:400;color:#222;margin-bottom:4px}
.f-col ul{list-style:none;font-size:9.5px;color:#666;line-height:17.5px}
.f-col li::before{content:"•";margin-right:6px;font-size:8px}
.col-quick{width:210px}
.col-quick .lists{display:flex;gap:58px}
.col-more{width:208px;padding-left:44px}
.col-app{width:312px;padding-left:38px}
.col-social{border:none;padding-left:49px}
.store-row{display:flex;gap:10px;margin-top:4px}
.store{width:116px;height:38px;border:1px solid #ccc;background:var(--white);display:flex;align-items:center;gap:6px;padding-left:9px;font-size:7px;line-height:9px;color:#444}
.store b{display:block;font-size:7.5px}
.store.dark{background:#1e1e1e;color:var(--white);border-color:#1e1e1e;width:115px}
.store i{width:14px;height:14px;border-radius:3px;background:currentColor;opacity:.5;flex:none}
.social{display:flex;gap:6px;margin-top:8px}
.social span{width:27px;height:27px;border-radius:50%}
.copyright{height:48px;background:var(--footer-bottom);color:#aaa;font-size:11.5px;text-align:center;line-height:48px}
</style>
</head>
<body>
<header class="site-header">
  <div class="wrap">
    <div class="brand"><span class="brand-dot"></span>FITBRISKO</div>
    <nav class="main-nav">
      <a href="#" class="active">My Diary</a>
      <a href="#">My Clubs</a>
      <a href="#">My Profile</a>
      <a href="#" class="btn btn-dark">Log in</a>
      <a href="#" class="btn btn-orange">Register</a>
    </nav>
  </div>
</header>

<section class="hero">
  <div class="hero-photo" role="img" aria-label="Photo of an athlete resting in a wheat field under a cloudy sky"></div>
  <div class="hero-intro">
    <h1>Welcome to Fitbrisko</h1>
    <p>Donec ac est nec felis tempor facilisis dictum quis mi. Sed ac purus eget dui ornare accumsan eget eget nibh. Ut euismod purus at ornare euismod. Suspendisse aliquam felis. Nam magna ex, commodo in eros et, dictum dictum justo.</p>
    <div class="hero-actions">
      <a href="#" class="btn btn-orange">Join an Event</a>
      <a href="#" class="btn btn-dark">Log in</a>
    </div>
  </div>

  <div class="events-panel">
    <div class="tabs">
      <div class="tab current">Events</div>
      <div class="tab">Calendar</div>
      <div class="tab">Nearby</div>
      <div class="tab-arrows">
        <span><svg width="8" height="10" viewBox="0 0 8 10"><path d="M6 1L2 5l4 4" fill="none" stroke="#fff" stroke-width="1.4"/></svg></span>
        <span><svg width="8" height="10" viewBox="0 0 8 10"><path d="M2 1l4 4-4 4" fill="none" stroke="#fff" stroke-width="1.4"/></svg></span>
      </div>
    </div>
    <div class="event-grid">
      <article class="event-card"><div class="club-badge" role="img" aria-label="Club badge" style="background:#8a1a10"></div><div class="event-body"><h3>Swim Training <small>- 8:15 PM</small></h3><p class="event-club">North Ridge Runners @ Hillcrest School</p><p class="event-desc">Freestyle (crawl) training comprising of warm up, drills and main set.</p><a href="#" class="btn btn-dark">Join an Event</a></div></article>
      <article class="event-card"><div class="club-badge" role="img" aria-label="Club badge" style="background:radial-gradient(circle,#d0264e 35%,#fff 37%)"></div><div class="event-body"><h3>Swim Training <small>- 8:15 PM</small></h3><p class="event-club">North Ridge Runners @ Hillcrest School</p><p class="event-desc">Freestyle (crawl) training comprising of warm up, drills and main set.</p><a href="#" class="btn btn-dark">Join an Event</a></div></article>
      <article class="event-card"><div class="club-badge" role="img" aria-label="Club badge" style="background:radial-gradient(circle,#d42a63 30%,#fff 32%)"></div><div class="event-body"><h3>Swim Training <small>- 8:15 PM</small></h3><p class="event-club">North Ridge Runners @ Hillcrest School</p><p class="event-desc">Freestyle (crawl) training comprising of warm up, drills and main set.</p><a href="#" class="btn btn-dark">Join an Event</a></div></article>
      <article class="event-card"><div class="club-badge" role="img" aria-label="Club badge" style="background:radial-gradient(circle,#e8642a 32%,#fff 34%)"></div><div class="event-body"><h3>Swim Training <small>- 8:15 PM</small></h3><p class="event-club">North Ridge Runners @ Hillcrest School</p><p class="event-desc">Freestyle (crawl) training comprising of warm up, drills and main set.</p><a href="#" class="btn btn-dark">Join an Event</a></div></article>
      <article class="event-card"><div class="club-badge" role="img" aria-label="Club badge" style="background:radial-gradient(circle,#5a86c8 30%,#fff 32%)"></div><div class="event-body"><h3>Swim Training <small>- 8:15 PM</small></h3><p class="event-club">North Ridge Runners @ Hillcrest School</p><p class="event-desc">Freestyle (crawl) training comprising of warm up, drills and main set.</p><a href="#" class="btn btn-dark">Join an Event</a></div></article>
      <article class="event-card"><div class="club-badge" role="img" aria-label="Club badge" style="background:radial-gradient(circle,#7a5cc8 34%,#fff 36%)"></div><div class="event-body"><h3>Swim Training <small>- 8:15 PM</small></h3><p class="event-club">North Ridge Runners @ Hillcrest School</p><p class="event-desc">Freestyle (crawl) training comprising of warm up, drills and main set.</p><a href="#" class="btn btn-dark">Join an Event</a></div></article>
    </div>
  </div>
</section>

<footer>
  <div class="site-footer">
    <div class="wrap">
      <div class="f-col col-quick">
        <h4>Quick Links</h4>
        <div class="lists">
          <ul><li>Home</li><li>My Diary</li><li>My Clubs</li></ul>
          <ul><li>My Profile</li><li>Register</li><li>Login</li></ul>
        </div>
      </div>
      <div class="f-col col-more">
        <h4>More Links</h4>
        <ul><li>Terms and Conditions</li><li>Privacy Policy</li><li>Sitemap</li></ul>
      </div>
      <div class="f-col col-app">
        <h4>Downlaod our App</h4>
        <div class="store-row">
          <div class="store"><i></i><span>Download it from<b>APP MARKET</b></span></div>
          <div class="store dark"><i></i><span>Download it from<b>APP SHELF</b></span></div>
        </div>
      </div>
      <div class="f-col col-social">
        <h4>Connect with us on</h4>
        <div class="social">
          <span style="background:#3b5998"></span>
          <span style="background:#29a9e1"></span>
          <span style="background:#0e76a8"></span>
          <span style="background:#f04a37"></span>
          <span style="background:#cb2027"></span>
        </div>
      </div>
    </div>
  </div>
  <div class="copyright">Copyright &copy; 2016 &nbsp;Fit Brisko. All rights reserved.</div>
</footer>
</body>
</html>
```